Product Designer Business Card

Small product design, engineering and prototyping firm in need of a clean, professional business card design. To support our 3D design and drawing services, we offer 3D printing, molding, and casting of plastics, silicones, resins, etc. Our logo can still be modified/changed if necessary. The red/orange color is preferred, but may be substituted with blue or green, potentially. Either way, the colour of the logo should be match/compliment colors used throughout the design. One thought is to have the logo/contact info on one side, with the other side describing services offered, like with a small icon of 3D printer, molding, casting, and computer with a 3D model on-screen.
Industry/Entity Type
Mechanical Engineering
Contact Information for Business Card
Company: Kelvar Design
Phone: 613-582-9047
Email: mark@kelvardesign.ca

```html
<!DOCTYPE html>
<html lang="en">
<head>
<meta charset="utf-8">
<title>Kelvar Design – Business Card</title>
<link href="https://fonts.googleapis.com/css2?family=Exo+2:ital,wght@0,400;0,600;1,700&display=swap" rel="stylesheet">
<style>
  :root {
    --page: #2a2a2b;
    --card: #1c1d1f;
    --red: #e0261b;
    --red-deep: #a8120c;
    --white: #eeeeee;
    --grey: #8a8a8c;
    --pattern-a: #232427;
    --pattern-b: #1c1d1f;
  }
  * { margin: 0; padding: 0; box-sizing: border-box; }
  html, body { width: 1200px; height: 1108px; overflow: hidden; }
  body {
    background: var(--page);
    font-family: "Exo 2", sans-serif;
    position: relative;
  }
  .card {
    position: absolute;
    top: 214px;
    width: 420px;
    height: 680px;
    background: var(--card);
    border-radius: 22px;
    box-shadow: 0 18px 40px rgba(0,0,0,.45);
    overflow: hidden;
  }
  .card-front { left: 150px; }
  .card-back { left: 630px; }

  /* front */
  .brand {
    position: absolute;
    top: 110px; left: 0; right: 0;
    display: flex; align-items: center; justify-content: center; gap: 18px;
  }
  .brand-dot {
    flex: none;
    width: 54px; height: 54px; border-radius: 50%;
    background: var(--red);
  }
  .brand-name {
    font-weight: 600; font-size: 44px; line-height: 1.1; color: var(--red);
    letter-spacing: 6px;
  }
  .brand-name span { display: block; }
  .person { position: absolute; top: 360px; left: 0; right: 0; text-align: center; }
  .person-name {
    font-weight: 700; font-style: italic; font-size: 30px;
    color: var(--red); text-transform: uppercase; letter-spacing: .5px;
  }
  .person-title { font-size: 21px; color: var(--white); margin-top: 2px; }
  .divider {
    position: absolute; top: 455px; left: 60px; right: 60px;
    display: flex; align-items: center; gap: 8px;
  }
  .divider-line { flex: 1; height: 1px; background: var(--grey); }
  .contact-icon {
    width: 26px; height: 26px; border-radius: 4px;
    background: var(--red-deep);
    display: flex; align-items: center; justify-content: center;
  }
  .contact { position: absolute; top: 500px; left: 0; right: 0; text-align: center; }
  .contact-line { font-size: 23px; color: var(--white); line-height: 34px; }
  .contact-line .accent { color: var(--red); }

  /* back */
  .pattern {
    position: absolute; inset: 0;
    background: linear-gradient(160deg, var(--pattern-a), var(--pattern-b));
  }
  .back-brand {
    position: absolute; top: 400px; right: 60px;
    display: flex; align-items: center; gap: 10px;
  }
  .back-brand .brand-dot { width: 40px; height: 40px; }
  .back-brand .brand-name { font-size: 36px; letter-spacing: 4px; }
  .services {
    position: absolute; top: 500px; left: 24px; right: 24px;
    display: flex; justify-content: space-between;
  }
  .service { width: 90px; text-align: center; }
  .service svg { width: 70px; height: 70px; display: block; margin: 0 auto 10px; }
  .service-label { font-size: 19px; color: var(--white); white-space: nowrap; }
</style>
</head>
<body>
  <section class="card card-front">
    <div class="brand">
      <span class="brand-dot"></span>
      <span class="brand-name"><span>Kelvar</span><span>Design</span></span>
    </div>
    <div class="person">
      <div class="person-name">Nolan Brecker</div>
      <div class="person-title">Managing Director</div>
    </div>
    <div class="divider">
      <span class="divider-line"></span>
      <span class="contact-icon">
        <svg width="16" height="16" viewBox="0 0 16 16"><path d="M3 2h3l1 3-2 1a8 8 0 0 0 5 5l1-2 3 1v3c-7 1-12-4-11-11z" fill="#fff"/></svg>
      </span>
      <span class="contact-icon">
        <svg width="16" height="16" viewBox="0 0 16 16"><rect x="1.5" y="3.5" width="13" height="9" fill="none" stroke="#fff" stroke-width="1.5"/><path d="M1.5 3.5l6.5 5 6.5-5" fill="none" stroke="#fff" stroke-width="1.5"/></svg>
      </span>
      <span class="contact-icon">
        <svg width="16" height="16" viewBox="0 0 16 16"><circle cx="8" cy="8" r="6" fill="none" stroke="#fff" stroke-width="1.5"/><path d="M2 8h12M8 2c-3 3-3 9 0 12M8 2c3 3 3 9 0 12" fill="none" stroke="#fff" stroke-width="1.2"/></svg>
      </span>
      <span class="divider-line"></span>
    </div>
    <div class="contact">
      <div class="contact-line">613-582-9047</div>
      <div class="contact-line">mark@kelvardesign.ca</div>
      <div class="contact-line">www.<span class="accent">kelvardesign</span>.ca</div>
    </div>
  </section>

  <section class="card card-back">
    <div class="pattern" role="img" aria-label="Faint repeating brand-name pattern background"></div>
    <div class="back-brand">
      <span class="brand-dot"></span>
      <span class="brand-name">Kelvar</span>
    </div>
    <div class="services">
      <div class="service">
        <svg viewBox="0 0 70 70"><rect x="8" y="8" width="54" height="50" fill="none" stroke="var(--red)" stroke-width="5"/><rect x="8" y="8" width="54" height="10" fill="var(--red)"/><rect x="22" y="26" width="26" height="6" fill="var(--red)"/><rect x="18" y="46" width="34" height="6" fill="var(--red)"/><path d="M35 32v10" stroke="var(--red)" stroke-width="4"/></svg>
        <div class="service-label">3D Printer</div>
      </div>
      <div class="service">
        <svg viewBox="0 0 70 70"><rect x="30" y="4" width="10" height="14" fill="var(--red)"/><rect x="16" y="18" width="38" height="10" fill="var(--red)"/><rect x="12" y="36" width="46" height="12" fill="var(--red)"/><rect x="8" y="56" width="54" height="8" fill="var(--red)"/><path d="M22 48v8M48 48v8" stroke="var(--red)" stroke-width="4"/></svg>
        <div class="service-label">Molding</div>
      </div>
      <div class="service">
        <svg viewBox="0 0 70 70"><path d="M10 10h22l-4 20H14z" fill="none" stroke="var(--red)" stroke-width="4"/><path d="M28 28q12 6 14 26" fill="none" stroke="var(--red)" stroke-width="5"/><rect x="26" y="54" width="36" height="10" fill="var(--red)"/></svg>
        <div class="service-label">Casting</div>
      </div>
      <div class="service">
        <svg viewBox="0 0 70 70"><rect x="6" y="8" width="58" height="40" rx="3" fill="var(--red)"/><rect x="11" y="13" width="48" height="30" fill="var(--card)"/><path d="M35 18l10 5v11l-10 5-10-5V23z M25 23l10 5 10-5 M35 28v11" fill="none" stroke="var(--red)" stroke-width="2.5"/><rect x="31" y="48" width="8" height="8" fill="var(--red)"/><rect x="20" y="56" width="30" height="5" fill="var(--red)"/></svg>
        <div class="service-label">3d Model</div>
      </div>
    </div>
  </section>
</body>
</html>
```